RTavenor Business Cards & Letterhead

I have a logo but need a design for some new business cards. We are a Design-Build Firm that specializes in the design and construction of commercial projects.
the cards need to be professional. no cartoon stuff.
i would like to have the cards in AI format so I can update the card as needed. Logo is provided.
Our Address is: 4187 Marlowe Ct. Ardvale, West Corland 27614

```html
<!DOCTYPE html>
<html lang="en">
<head>
<meta charset="utf-8">
<title>RTavenor Business Card</title>
<link rel="stylesheet" href="https://fonts.googleapis.com/css2?family=Arimo:wght@400;700&display=swap">
<style>
  :root {
    --bg: #e4e4e4;
    --paper: #f4f4f3;
    --ink: #1d1d1f;
    --brand-blue: #0f5fa8;
    --edge-blue: #1672c4;
    --back-dark: #1b1b1c;
    --back-mid: #2e2e30;
  }
  * { box-sizing: border-box; margin: 0; padding: 0; }
  html, body { width: 1200px; height: 1200px; overflow: hidden; }
  body {
    background: var(--bg);
    font-family: "Arimo", Arial, sans-serif;
    color: var(--ink);
    position: relative;
  }
  .card {
    position: absolute;
    left: 150px;
    width: 900px;
    height: 514px;
    border-bottom: 5px solid var(--edge-blue);
    border-right: 3px solid var(--edge-blue);
    box-shadow: 0 14px 30px rgba(0,0,0,0.18);
  }
  .card--front { top: 70px; background: var(--paper); }
  .card--back {
    top: 616px;
    background: linear-gradient(135deg, var(--back-dark) 0%, var(--back-mid) 100%);
  }
  .wordmark {
    position: absolute;
    left: 80px;
    top: 232px;
    display: flex;
    align-items: center;
    gap: 12px;
    font-size: 40px;
    font-weight: 700;
    letter-spacing: 1px;
    color: var(--ink);
  }
  .wordmark__square {
    width: 30px; height: 30px;
    background: var(--brand-blue);
  }
  .divider {
    position: absolute;
    left: 405px;
    top: 110px;
    width: 1.5px;
    height: 300px;
    background: var(--ink);
  }
  .details {
    position: absolute;
    left: 440px;
    top: 112px;
  }
  .details__name {
    font-size: 34px;
    font-weight: 700;
    color: var(--brand-blue);
  }
  .details__title {
    font-size: 20px;
    margin-top: 6px;
  }
  .details__address {
    font-size: 21px;
    line-height: 1.35;
    margin-top: 34px;
  }
  .contact-list {
    list-style: none;
    margin-top: 20px;
    font-size: 21px;
    line-height: 1.55;
  }
  .contact-list li { display: flex; align-items: center; gap: 8px; }
  .contact-list svg { width: 15px; height: 15px; fill: var(--brand-blue); }
</style>
</head>
<body>
  <section class="card card--front">
    <div class="wordmark"><span class="wordmark__square"></span>RTAVENOR</div>
    <div class="divider"></div>
    <div class="details">
      <h1 class="details__name">Rhett Tavenor</h1>
      <p class="details__title">CEO</p>
      <p class="details__address">4187 Marlowe Ct. Ardvale,<br>West Corland 27614</p>
      <ul class="contact-list">
        <li><svg viewBox="0 0 16 16"><path d="M3 1l3 3-1.5 2a9 9 0 0 0 5.5 5.5L12 10l3 3-2 2C7 15 1 9 1 3z"/></svg>201.555.0148</li>
        <li><svg viewBox="0 0 16 16"><path d="M4 0h8a1 1 0 0 1 1 1v14a1 1 0 0 1-1 1H4a1 1 0 0 1-1-1V1a1 1 0 0 1 1-1zm1 2v10h6V2z"/></svg>201.555.0193</li>
        <li><svg viewBox="0 0 16 16"><path d="M0 3h16v10H0zm1 1l7 5 7-5"/></svg>rhett@rtavenor.com</li>
        <li><svg viewBox="0 0 16 16"><circle cx="8" cy="8" r="7.5"/></svg>www.rtavenor.com</li>
      </ul>
    </div>
  </section>
  <section class="card card--back" role="img" aria-label="Repeating embossed brand-mark pattern on dark card back"></section>
</body>
</html>
```